Wandering Rooms Stationary Set

Wandering Rooms is a bespoke interior design firm set to provide services to VIP clients with elegance and minimalism is the main theme for our stationary set. We require a full stationary set covering A4 letterhead, A4 & A3 envelopes, business cards, USB's, CDs, email signature and any other item the designer sees fit. logo is already designed and finalized, and we require the designer to use it as is without modifying the logo.

Address to be used on letterhead / business cards ...etc shall be as follows:

Phone : +971 2 518 2047
P.O. Box : 309186
Address: Block C&D, Bldg. 47, Court 12, Abu Dhabi, United Arab Emirates
Website: www.wanderingrooms-example.com

Target Market(s)

VIP Clients

Industry/Entity Type

Interior Design

Font styles to use
Other font styles liked:
• something to be unique

Colors

Designer to choose colors to be used in the design.

Requirements
Must have
• Elegant, minimalistic
Nice to have
• Simple yet elegant design having a sharp yet clean cut format
Should not have
• No additional colours, just colours that are used in the logo (silver, black or gold)

```html
<!DOCTYPE html>
<html lang="en">
<head>
<meta charset="utf-8">
<title>Wandering Rooms – Business Card</title>
<link rel="stylesheet" href="https://fonts.googleapis.com/css2?family=Cormorant+Garamond:wght@400;500&family=Allura&display=swap">
<style>
  :root {
    --backdrop: #1b1b1b;
    --card: #262524;
    --gold: #c9a24a;
    --silver: #9c9c9c;
    --text-grey: #a8a6a2;
    --text-light: #d6d3cd;
  }
  * { margin: 0; padding: 0; box-sizing: border-box; }
  html, body {
    width: 1200px; height: 800px; overflow: hidden;
    background: var(--backdrop);
    font-family: "Cormorant Garamond", Georgia, serif;
  }
  .sheet {
    position: relative; width: 1200px; height: 800px;
    display: flex; align-items: center; justify-content: center; gap: 60px;
  }
  .card {
    position: relative; width: 520px; height: 297px;
    background: var(--card);
    box-shadow: 0 10px 30px rgba(0,0,0,.45);
  }
  /* front */
  .card-front { display: flex; align-items: center; justify-content: center; }
  .brand-name {
    font-family: "Cormorant Garamond", Georgia, serif;
    font-weight: 400; letter-spacing: 6px; text-transform: uppercase;
    white-space: nowrap;
  }
  .card-front .brand-name { color: var(--silver); font-size: 34px; }
  /* back */
  .card-back .brand-name {
    position: absolute; left: 40px; top: 74px;
    color: var(--gold); font-size: 24px; letter-spacing: 5px;
  }
  .person {
    position: absolute; right: 40px; top: 34px; text-align: right;
  }
  .person-name {
    font-family: "Allura", cursive; color: var(--gold); font-size: 30px; line-height: 1;
  }
  .person-role { color: var(--text-light); font-size: 15px; margin-top: 2px; }
  .contact {
    position: absolute; right: 40px; top: 168px; text-align: right;
    color: var(--text-grey); font-size: 12.5px; line-height: 1.45;
  }
  .contact .label { color: var(--gold); font-weight: 500; }
  .rule {
    position: absolute; left: 40px; right: 40px; top: 212px;
    height: 1px; background: var(--gold); opacity: .8;
  }
  .address {
    position: absolute; left: 40px; top: 160px;
    color: var(--text-grey); font-size: 12.5px; line-height: 1.35;
  }
  .website {
    position: absolute; left: 40px; top: 224px;
    color: var(--gold); font-size: 12.5px; letter-spacing: 2px;
  }
</style>
</head>
<body>
<main class="sheet">
  <section class="card card-front">
    <p class="brand-name">Wandering Rooms</p>
  </section>

  <section class="card card-back">
    <p class="brand-name">Wandering Rooms</p>
    <div class="person">
      <p class="person-name">Daniel Harlow</p>
      <p class="person-role">President</p>
    </div>
    <div class="address">
      <p>P.O. Box : 309186</p>
      <p>Block C&amp;D, Bldg. 47, Court 12</p>
      <p>Abu Dhabi, United Arab Emirate</p>
    </div>
    <div class="contact">
      <p><span class="label">P :</span> +971 2 518 2047</p>
      <p><span class="label">E :</span> info@wanderingrooms-example.com</p>
    </div>
    <div class="rule"></div>
    <p class="website">www.wanderingrooms-example.com</p>
  </section>
</main>
</body>
</html>
```